Direct Mail Condition Reporting Flyer

This is a quality control service that is designed to
detect direct mail such as letters, magazines and catalogs that are delivered by the Vellmark Courier Bureau in poor condition. Attached are actual samples of mail delivered in poor condition and our company logo. We generally use the Red and Blue colors of the Vellmark Courier Bureau.

Target Market(s)

Direct mailers from every Industry

Industry/Entity Type

It Service

Font styles to use
Sans Serif

Colors
ec1f27
0555a3

Requirements
Must have
• It needs to look professional. It will be placed on a table at a trade conference and inserted into a folder with other material.

```html
<!DOCTYPE html>
<html lang="en">
<head>
<meta charset="utf-8">
<title>Kessly Mailcheck – Mail Condition Reporting</title>
<link href="https://fonts.googleapis.com/css2?family=Poppins:wght@600;700&family=Roboto+Condensed:wght@400;700&display=swap" rel="stylesheet">
<style>
  :root {
    --brand-red: #c8193a;
    --signal-red: #ec1f27;
    --brand-blue: #1d3f8f;
    --ink-grey: #7a7a7a;
    --paper: #ffffff;
  }
  * { margin: 0; padding: 0; box-sizing: border-box; }
  html, body { width: 773px; height: 1200px; overflow: hidden; background: var(--paper); }
  .flyer {
    position: relative; width: 773px; height: 1200px; overflow: hidden;
    background: var(--paper); font-family: "Roboto Condensed", Arial, sans-serif;
  }
  .flap-lines { position: absolute; top: 0; left: 0; width: 773px; height: 404px; }
  .brand {
    position: absolute; top: 122px; left: 0; width: 100%; text-align: center;
    display: flex; justify-content: center; align-items: center; gap: 10px;
  }
  .brand-mark { width: 14px; height: 14px; background: var(--brand-blue); }
  .brand-name {
    font-family: "Poppins", Arial, sans-serif; font-weight: 600; font-size: 28px;
    line-height: 36px; color: var(--brand-blue);
  }
  .tagline {
    position: absolute; top: 178px; left: 0; width: 100%; text-align: center;
    font-family: "Roboto Condensed", Arial, sans-serif; font-weight: 400;
    font-size: 15px; color: var(--ink-grey);
  }
  .headline {
    position: absolute; top: 243px; left: 0; width: 100%; text-align: center;
    font-family: "Poppins", Arial, sans-serif; font-weight: 700; font-size: 43px;
    line-height: 46px; color: var(--ink-grey);
  }
  .red-band { position: absolute; top: 357px; left: 0; width: 100%; height: 47px; background: var(--brand-red); }
  .blue-field { position: absolute; top: 404px; left: 0; width: 100%; height: 796px; background: var(--brand-blue); }
  .mail-photo { position: absolute; }
  .mail-photo--hero { top: 371px; left: 7px; width: 570px; height: 325px; }
  .mail-photo--stack { top: 715px; left: 396px; width: 377px; height: 468px; }
  .checklist {
    position: absolute; top: 800px; left: 29px; width: 340px; list-style: none;
    color: var(--paper); font-size: 12px; line-height: 14px; font-weight: 700;
  }
  .checklist li { position: relative; padding-left: 24px; margin-bottom: 14px; }
  .checklist svg { position: absolute; left: 0; top: 0; width: 16px; height: 16px; }
  .quote-badge {
    position: absolute; left: 530px; top: 883px; width: 238px; height: 238px;
    border-radius: 50%; background: var(--signal-red); opacity: 0.88;
    display: flex; align-items: center; justify-content: center; text-align: center;
    padding: 0 30px; color: var(--paper); font-size: 14px; line-height: 16px;
  }
  .quote-badge strong { font-weight: 700; }
</style>
</head>
<body>
<main class="flyer">
  <svg class="flap-lines" viewBox="0 0 773 404" aria-hidden="true">
    <line x1="0" y1="0" x2="386" y2="357" stroke="#d9d9d9" stroke-width="1" stroke-dasharray="4 3"/>
    <line x1="773" y1="0" x2="386" y2="357" stroke="#d9d9d9" stroke-width="1" stroke-dasharray="4 3"/>
  </svg>

  <header class="brand">
    <span class="brand-mark"></span><span class="brand-name">Kessly Mailcheck</span>
  </header>
  <p class="tagline">Insight that keeps every mailing on track.</p>
  <h1 class="headline">How much of your mail is<br>being delivered like this?</h1>

  <div class="red-band"></div>
  <div class="blue-field"></div>

  <svg class="mail-photo mail-photo--hero" viewBox="0 0 570 325" role="img" aria-label="Photo of a torn and crumpled catalog envelope delivered in poor condition">
    <defs>
      <linearGradient id="heroTone" x1="0" y1="0" x2="1" y2="1">
        <stop offset="0" stop-color="#c98a5c"/>
        <stop offset="0.45" stop-color="#e6dccf"/>
        <stop offset="1" stop-color="#f1f1ee"/>
      </linearGradient>
    </defs>
    <polygon points="40,70 110,10 430,15 570,55 545,235 360,290 110,320 0,250" fill="url(#heroTone)"/>
  </svg>

  <svg class="mail-photo mail-photo--stack" viewBox="0 0 377 468" role="img" aria-label="Photo of a stack of damaged, creased and torn letters and mailers">
    <defs>
      <linearGradient id="stackTone" x1="0" y1="0" x2="1" y2="1">
        <stop offset="0" stop-color="#eeeeea"/>
        <stop offset="1" stop-color="#c9c9c4"/>
      </linearGradient>
    </defs>
    <polygon points="120,0 330,20 345,170 377,190 377,460 170,468 50,450 0,250 50,130 110,120" fill="url(#stackTone)"/>
  </svg>

  <ul class="checklist">
    <li><svg viewBox="0 0 16 16"><path d="M2 9 L6 13 L14 2" fill="none" stroke="#fff" stroke-width="2.2"/></svg>Is poor condition affecting the delivery of your mail?</li>
    <li><svg viewBox="0 0 16 16"><path d="M2 9 L6 13 L14 2" fill="none" stroke="#fff" stroke-width="2.2"/></svg>Will your company's reputation suffer when customers receive damaged mailings?</li>
    <li><svg viewBox="0 0 16 16"><path d="M2 9 L6 13 L14 2" fill="none" stroke="#fff" stroke-width="2.2"/></svg>Are missing inserts hurting our response rate?</li>
    <li><svg viewBox="0 0 16 16"><path d="M2 9 L6 13 L14 2" fill="none" stroke="#fff" stroke-width="2.2"/></svg>Kessly Mailcheck has developed a comprehensive mail condition reporting service that answers these questions in response to the increased incidence of mailings being delivered in poor condition. You learn:</li>
    <li><svg viewBox="0 0 16 16"><path d="M2 9 L6 13 L14 2" fill="none" stroke="#fff" stroke-width="2.2"/></svg>If your direct mail or catalogs are received torn, creased, smudged, wrinkled, stained or with water damage.</li>
    <li><svg viewBox="0 0 16 16"><path d="M2 9 L6 13 L14 2" fill="none" stroke="#fff" stroke-width="2.2"/></svg>Whether there are printing errors or problems with ink jetting and addressing.</li>
    <li><svg viewBox="0 0 16 16"><path d="M2 9 L6 13 L14 2" fill="none" stroke="#fff" stroke-width="2.2"/></svg>If contents are missing after mail is opened.</li>
  </ul>

  <aside class="quote-badge">
    <p>You have the ability to receive scanned images or to have the damaged pieces returned. Custom programs are available. <strong>Request a quote at kesslymailcheck.com/condition or call 555.014.2290.</strong></p>
  </aside>
</main>
</body>
</html>
```